Classy, Elegant, Simple Business Card Design

Looking to have a classy, simple, and elegant design. Want a top notch designed business card. I really like the look of the new torvane credit card. I also like the design I attached. I am trying to reach 21-29 year old females for booking us for there wedding or event. We offer Disc Jockey Service, Photo Booth Rentals, and Uplighting .

Target Market(s)

21-28 year old females

Contact Information for Business Card

Has to have logo, website, email, and phone number

Font styles to use
Other font styles liked:
• open to font choice, modern, clean
Designer to choose
33a6d7
0791cd
0555a3
ffffff

Requirements
Must have
• Has to have logo, website, email, and phone number
Nice to have
• I really like the design of the new torvane credit card. I also included my logo and some designs I like
Should not have
• clutter or too much info

```html
<!DOCTYPE html>
<html lang="en">
<head>
<meta charset="utf-8">
<title>Tidewell Event Group – Business Card</title>
<link href="https://fonts.googleapis.com/css2?family=Jost:wght@300;400&family=Oswald:wght@400&family=Work+Sans:wght@400&display=swap" rel="stylesheet">
<style>
  :root {
    --backdrop: #151515;
    --card: #1e1e1e;
    --card-edge: #2a2a2a;
    --silver: #c9c9c9;
    --silver-soft: #a9a9a9;
    --silver-dim: #8c8c8c;
  }
  * { margin: 0; padding: 0; box-sizing: border-box; }
  html, body {
    width: 1200px; height: 900px; overflow: hidden;
    background: var(--backdrop);
  }
  .canvas {
    position: relative; width: 1200px; height: 900px;
    display: flex; flex-direction: column; align-items: center; justify-content: center;
    gap: 40px;
  }
  .card {
    position: relative; width: 640px; height: 366px;
    background: linear-gradient(135deg, #1b1b1b 0%, var(--card) 55%, #262626 100%);
    border: 1px solid var(--card-edge);
    box-shadow: 0 18px 40px rgba(0,0,0,0.6);
  }
  /* Front */
  .card-front {
    display: flex; flex-direction: column; align-items: center; justify-content: center;
  }
  .brand-name {
    font-family: "Jost", sans-serif; font-weight: 400;
    font-size: 48px; letter-spacing: 4px; color: var(--silver);
    text-transform: uppercase; line-height: 1;
  }
  .brand-tagline {
    margin-top: 10px;
    font-family: "Jost", sans-serif; font-weight: 300;
    font-size: 15px; letter-spacing: 9px; color: var(--silver-soft);
    text-transform: uppercase;
  }
  /* Back */
  .card-back { display: flex; flex-direction: column; }
  .back-main {
    flex: 1; display: flex; align-items: center; justify-content: center; gap: 34px;
    padding-top: 40px;
  }
  .person { text-align: right; }
  .person-name {
    font-family: "Oswald", sans-serif; font-weight: 400;
    font-size: 34px; letter-spacing: 1.5px; color: var(--silver);
    text-transform: uppercase; line-height: 1.1;
  }
  .person-role {
    font-family: "Work Sans", sans-serif; font-size: 15px;
    color: var(--silver-soft); letter-spacing: 0.5px;
  }
  .divider { width: 1px; height: 78px; background: var(--silver-dim); }
  .contact-list { list-style: none; display: flex; flex-direction: column; gap: 6px; }
  .contact-item {
    display: flex; align-items: center; gap: 10px;
    font-family: "Work Sans", sans-serif; font-size: 16px;
    color: var(--silver); letter-spacing: 0.6px;
  }
  .contact-icon { width: 12px; height: 12px; flex: none; }
  .address {
    padding: 0 0 36px 40px;
    font-family: "Work Sans", sans-serif; font-size: 16px;
    color: var(--silver-soft); letter-spacing: 0.6px;
  }
</style>
</head>
<body>
<main class="canvas">
  <section class="card card-front" aria-label="Card front">
    <div class="brand-name">Tidewell</div>
    <div class="brand-tagline">Event Group</div>
  </section>

  <section class="card card-back" aria-label="Card back">
    <div class="back-main">
      <div class="person">
        <div class="person-name">Darren Hollis</div>
        <div class="person-role">Managing Partner</div>
      </div>
      <div class="divider"></div>
      <ul class="contact-list">
        <li class="contact-item">
          <svg class="contact-icon" viewBox="0 0 24 24" aria-hidden="true"><path fill="#c9c9c9" d="M6.6 10.8a15.1 15.1 0 0 0 6.6 6.6l2.2-2.2a1 1 0 0 1 1-.25 11.4 11.4 0 0 0 3.6.57 1 1 0 0 1 1 1V20a1 1 0 0 1-1 1A17 17 0 0 1 3 4a1 1 0 0 1 1-1h3.5a1 1 0 0 1 1 1c0 1.25.2 2.45.57 3.57a1 1 0 0 1-.25 1z"/></svg>
          615-555-0182
        </li>
        <li class="contact-item">
          <svg class="contact-icon" viewBox="0 0 24 24" aria-hidden="true"><rect x="2.5" y="5" width="19" height="14" fill="none" stroke="#c9c9c9" stroke-width="2"/><path d="M3 6l9 7 9-7" fill="none" stroke="#c9c9c9" stroke-width="2"/></svg>
          info@tidewell.com
        </li>
        <li class="contact-item">
          <svg class="contact-icon" viewBox="0 0 24 24" aria-hidden="true"><g fill="none" stroke="#c9c9c9" stroke-width="2"><circle cx="12" cy="12" r="9.5"/><ellipse cx="12" cy="12" rx="4" ry="9.5"/><path d="M2.5 12h19"/></g></svg>
          www.tidewell.com
        </li>
      </ul>
    </div>
    <div class="address">418 W Maple Ave., Pasadena, CA 91105</div>
  </section>
</main>
</body>
</html>
```